Varentoria Business Card and Letter Head

We are a leadership assessment consultancy based in Sydney, Australia. We help executive-level decison-makers select leaders for more senior level roles in corporate and government organisations. Our methodology is based on the latest research from the field of neuroscience.
We need a business card design and matching letter head that presents our company, Varentoria, as a:
1. trusted adviser to senior executive-level decison makers
2. niche consultancy who are experts in the field of assessing leadership talent
3. results-focused solution provider who balance scientific methods with pragmatic solutions
The following company details should be used in all designs:
Company Name: Varentoria
Details (for business card):
Derek Hanford
Prime Capacity Officer
Level 29, Marlow Tower
7 Marlow Square
Sydney, NSW 2000 Australia
Phone: 1300 582 714
Mobile: 0412 637 258
Email: derek.hanford@varentoria-example.com.au
Website: varentoria-example.com.au
I have attached the logo for Varentoria (for both a white and black background) - your business card and letter head designs must incoporate this logo and colour scheme.
Thanks for your interest in this project, I'm looking forward to receiving your ideas.
Regards,
Derek
Target Market(s)
Executive-level decison-makers in corporate and government organisations (e.g., CEO, VP, Head of Human Resources)
Industry/Entity Type
Leadership
Look and feel

```html
<!DOCTYPE html>
<html lang="en">
<head>
<meta charset="utf-8">
<title>Varentoria Business Card</title>
<link rel="stylesheet" href="https://fonts.googleapis.com/css2?family=Source+Sans+3:wght@400;600;700&display=swap">
<style>
  :root {
    --bg: #e8e5e1;
    --card: #ffffff;
    --ink: #3c3c3c;
    --ink-soft: #5a5a5a;
    --accent: #b3281d;
    --rule: #c8c8c8;
    --shadow: rgba(0, 0, 0, 0.14);
  }
  * { box-sizing: border-box; margin: 0; padding: 0; }
  html, body {
    width: 1200px;
    height: 1094px;
    overflow: hidden;
    background: var(--bg);
    font-family: "Source Sans 3", "Myriad Pro", Arial, sans-serif;
    color: var(--ink);
  }
  .canvas {
    position: relative;
    width: 1200px;
    height: 1094px;
  }
  .card {
    position: absolute;
    left: 160px;
    width: 880px;
    height: 500px;
    background: var(--card);
    border-radius: 36px;
    box-shadow: 0 6px 18px var(--shadow);
    overflow: hidden;
  }
  .card--front { top: 36px; }
  .card--back { top: 558px; }

  .brand {
    position: absolute;
    display: flex;
    flex-direction: column;
  }
  .brand__row {
    display: flex;
    align-items: center;
  }
  .brand__square {
    background: var(--accent);
    flex: none;
  }
  .brand__name {
    font-weight: 700;
    color: var(--ink);
    letter-spacing: -0.01em;
    line-height: 1;
  }
  .brand__tagline {
    color: var(--ink-soft);
    font-weight: 400;
    text-transform: uppercase;
    letter-spacing: 0.06em;
    line-height: 1;
    white-space: nowrap;
  }

  .card--front .brand { left: 64px; top: 196px; }
  .card--front .brand__square { width: 40px; height: 40px; margin-right: 14px; }
  .card--front .brand__name { font-size: 50px; }
  .card--front .brand__tagline { font-size: 15px; margin-top: 8px; margin-left: 54px; }

  .card--back .brand { left: 0; right: 0; top: 170px; align-items: center; }
  .card--back .brand__square { width: 70px; height: 70px; margin-right: 22px; }
  .card--back .brand__name { font-size: 96px; }
  .card--back .brand__tagline { font-size: 26px; margin-top: 14px; margin-left: 92px; }

  .divider {
    position: absolute;
    left: 448px;
    top: 72px;
    width: 3px;
    height: 250px;
    background: linear-gradient(to bottom, rgba(200,200,200,0), var(--rule) 25%, var(--rule) 75%, rgba(200,200,200,0));
  }

  .contact {
    position: absolute;
    left: 476px;
    top: 66px;
  }
  .contact__name {
    font-size: 30px;
    font-weight: 700;
    color: var(--accent);
    line-height: 1.1;
  }
  .contact__title {
    font-size: 18px;
    color: var(--ink);
    margin-top: 2px;
  }
  .contact__list {
    list-style: none;
    margin-top: 34px;
  }
  .contact__item {
    display: flex;
    align-items: center;
    font-size: 18px;
    color: var(--ink);
    height: 30px;
    white-space: nowrap;
  }
  .contact__icon {
    width: 18px;
    height: 18px;
    margin-right: 12px;
    flex: none;
  }

  .address {
    position: absolute;
    left: 0;
    right: 0;
    top: 410px;
    text-align: center;
    font-size: 20px;
    color: var(--accent);
  }
</style>
</head>
<body>
<main class="canvas">

  <section class="card card--front" aria-label="Business card, front">
    <div class="brand">
      <div class="brand__row">
        <span class="brand__square"></span>
        <span class="brand__name">Varentoria</span>
      </div>
      <span class="brand__tagline">Selecting Tomorrow's Leaders</span>
    </div>

    <span class="divider"></span>

    <div class="contact">
      <p class="contact__name">Derek Hanford</p>
      <p class="contact__title">Prime Capacity Officer</p>
      <ul class="contact__list">
        <li class="contact__item">
          <svg class="contact__icon" viewBox="0 0 18 18" aria-hidden="true">
            <circle cx="9" cy="9" r="8" fill="none" stroke="#3c3c3c" stroke-width="1.4"/>
            <path d="M6.3 5.2c.4-.4 1-.3 1.2.2l.6 1.3c.2.4 0 .8-.3 1.1l-.4.3c.5 1.1 1.3 2 2.4 2.5l.3-.4c.3-.3.7-.4 1.1-.2l1.3.6c.5.2.6.8.2 1.2l-.6.6c-.6.6-1.6.7-2.5.2-2-1.1-3.5-2.7-4.4-4.6-.4-.9-.3-1.8.3-2.4z" fill="#3c3c3c"/>
          </svg>
          1300 582 714
        </li>
        <li class="contact__item">
          <svg class="contact__icon" viewBox="0 0 18 18" aria-hidden="true">
            <rect x="5" y="1.5" width="8" height="15" rx="1.5" fill="none" stroke="#3c3c3c" stroke-width="1.4"/>
            <rect x="6.5" y="3.5" width="5" height="6" fill="#3c3c3c"/>
            <circle cx="9" cy="13.3" r="1" fill="#3c3c3c"/>
          </svg>
          0412 637 258
        </li>
        <li class="contact__item">
          <svg class="contact__icon" viewBox="0 0 18 18" aria-hidden="true">
            <rect x="1.5" y="4" width="15" height="10.5" rx="1" fill="#3c3c3c"/>
            <path d="M2 4.6 9 10l7-5.4" fill="none" stroke="#ffffff" stroke-width="1.2"/>
          </svg>
          derek.hanford@varentoria-example.com.au
        </li>
        <li class="contact__item">
          <svg class="contact__icon" viewBox="0 0 18 18" aria-hidden="true">
            <circle cx="9" cy="9" r="7.5" fill="#3c3c3c"/>
            <ellipse cx="9" cy="9" rx="3.2" ry="7.5" fill="none" stroke="#ffffff" stroke-width="1"/>
            <path d="M1.5 9h15M3 5h12M3 13h12" stroke="#ffffff" stroke-width="1"/>
          </svg>
          www.varentoria-example.com.au
        </li>
      </ul>
    </div>

    <p class="address">Level 29, Marlow Tower 7 Marlow Square Sydney, NSW 2000 Australia</p>
  </section>

  <section class="card card--back" aria-label="Business card, back">
    <div class="brand">
      <div class="brand__row">
        <span class="brand__square"></span>
        <span class="brand__name">Varentoria</span>
      </div>
      <span class="brand__tagline">Selecting Tomorrow's Leaders</span>
    </div>
  </section>

</main>
</body>
</html>
```